13 Varno - new website design project

Our company Varno Electrical is developing a new lead generation website focused on Electrical, LED Lighting and Solar Power. We need a high converting website.

Example of our current website is www.varnoelectrical-example.com.au You can take content from this website for this new design. Our colours are red, black and white. For our new website we would like to promote Varno, Spark Every Day. Please listen to the jingle.

The below link is the company jingle that we have developed.
http://www.tunecraftdemo.com.au/vrn-tc-v1/

The key for this brief is to generate leads for Electrical, LED Lighting (for commercial) and Solar Power & Storage.

Target Market(s)

Business owners in Melbourne Victoria

Number of Pages Required

4 page

Colors
ec1f27
ffffff

Requirements
Must have
• This page must be clean, be in line with company branding and a high converting lead website.

```html
<!DOCTYPE html>
<html lang="en">
<head>
<meta charset="utf-8">
<title>Varno Electrical – Spark Every Day</title>
<link href="https://fonts.googleapis.com/css2?family=Raleway:wght@400;500;600;700&family=Open+Sans:ital,wght@0,400;0,600;0,700;1,400&display=swap" rel="stylesheet">
<style>
:root{
  --red:#ec1f27;
  --red-dark:#c8141b;
  --ink:#1d1d1d;
  --text:#444;
  --muted:#6b6b6b;
  --light:#f0f0f0;
  --footer:#ebebeb;
  --white:#fff;
}
*{box-sizing:border-box;margin:0;padding:0}
html,body{width:1200px;height:3051px;overflow:hidden}
body{background:var(--white);font-family:"Open Sans",Arial,sans-serif;color:var(--text);position:relative}
.block{position:absolute}
h1,h2,h3,h4{font-family:"Raleway",Arial,sans-serif;color:var(--ink)}

/* header */
.site-header{position:absolute;top:0;left:0;width:1200px;height:114px;background:var(--white)}
.brand{position:absolute;left:162px;top:24px;display:flex;align-items:center;gap:8px}
.brand-mark{width:26px;height:26px;border-radius:50%;background:var(--red);flex:none}
.brand-name{font-family:"Raleway",sans-serif;font-weight:700;font-size:34px;color:var(--ink);line-height:1}
.brand-tag{position:absolute;left:162px;top:66px;font-size:11px;font-weight:600;color:var(--ink)}
.call{position:absolute;right:160px;top:24px;font-family:"Raleway",sans-serif;font-weight:700;font-size:15px;color:var(--red);display:flex;align-items:center;gap:8px}
.main-nav{position:absolute;right:160px;top:74px;display:flex;gap:35px;font-family:"Raleway",sans-serif;font-weight:700;font-size:11.5px;color:var(--ink);text-transform:uppercase}
.main-nav .active{color:var(--red)}

/* hero */
.hero{position:absolute;top:114px;left:0;width:1200px;height:534px;background:linear-gradient(180deg,#6f7f8f 0%,#a8a59a 30%,#4b5966 55%,#2f3d4c 75%,#6b5a32 100%)}
.hero-title{position:absolute;top:84px;width:100%;text-align:center;font-family:"Raleway",sans-serif;font-weight:600;font-size:44px;line-height:56px;color:var(--white)}
.btn{display:inline-block;font-family:"Raleway",sans-serif;font-weight:700;text-transform:uppercase;border-radius:22px}
.hero .btn{position:absolute;left:512px;top:210px;width:176px;height:42px;line-height:38px;text-align:center;background:var(--red);color:var(--white);font-size:12px;border:2px solid #f06a6f}
.hero-arrow{position:absolute;top:240px}

/* section titles */
.section-title{font-weight:500;font-size:26px;line-height:32px;text-transform:uppercase}
.rule{display:block;width:98px;height:6px;border-top:2px solid var(--red);border-bottom:2px solid var(--red);margin-top:12px}
.center{text-align:center}
.center .rule{margin-left:auto;margin-right:auto}

/* about */
.about-copy{left:160px;top:706px;width:385px}
.about-copy p{margin-top:22px;font-size:11px;line-height:20.5px;text-align:justify}
.btn-outline{margin-top:16px;width:98px;height:36px;line-height:32px;text-align:center;border:2px solid var(--red);color:var(--red);font-size:10.5px}
.about-video{position:absolute;left:565px;top:712px;width:475px;height:304px;background:linear-gradient(160deg,#cfd3d8,#7a8593 60%,#3d4550)}
.about-video svg{display:block}

/* services */
.services{position:absolute;top:1076px;left:0;width:1200px;height:477px;background:var(--light);border-top:1px solid #ddd;border-bottom:1px solid #ddd}
.service{position:absolute;top:56px;width:276px}
.service-photo{height:202px}
.service h3{margin-top:22px;font-weight:500;font-size:25px;line-height:30px}
.service .rule{width:110px}
.service p{margin-top:16px;font-size:10.5px;line-height:21px}

/* why */
.why-title{left:160px;top:1628px;width:880px}
.reason{position:absolute;top:1715px;width:170px;text-align:center}
.badge{width:74px;height:74px;margin:0 auto;border-radius:50%;background:var(--red);border:3px solid var(--white);box-shadow:0 0 0 2px var(--red);color:var(--white);font-family:"Raleway",sans-serif;font-size:28px;line-height:68px}
.reason h4{margin-top:24px;font-family:"Open Sans",sans-serif;font-weight:600;font-size:12.5px;line-height:17px;height:34px;padding:0 22px}
.reason p{margin-top:6px;font-size:10.5px;line-height:19.5px;padding:0 8px}

/* reviews */
.reviews{position:absolute;top:2000px;left:0;width:1200px;height:405px;background:var(--red)}
.reviews .section-title{color:var(--white)}
.reviews .rule{border-color:var(--white);width:110px}
.reviews-title{left:160px;top:72px}
.quote{position:absolute;left:160px;top:128px;width:480px;display:flex;gap:14px}
.quote-mark{font-family:Georgia,serif;font-weight:700;font-size:60px;line-height:40px;color:var(--white);flex:none}
.quote p{font-style:italic;font-size:11.5px;line-height:22px;color:var(--white)}
.reviewer{position:absolute;left:162px;top:310px;color:var(--white);font-size:13px}
.reviewer .stars{letter-spacing:2px;margin-right:8px}
.review-card{position:absolute;left:668px;top:80px;width:372px;height:240px;background:var(--white);padding:6px}
.review-card-name{height:64px;display:flex;align-items:center;gap:10px;padding-left:8px;font-family:"Raleway",sans-serif;font-weight:700;font-size:24px;color:#555}
.review-card-name i{width:30px;height:30px;background:#555;display:block}
.review-card-photo{height:164px;background:linear-gradient(180deg,#9aa0a6,#6e6258 60%,#8a7258)}

/* clients */
.clients-title{left:160px;top:2452px;width:880px}
.client{position:absolute;top:2545px;width:166px;height:96px;display:flex;align-items:center;justify-content:center;font-family:"Raleway",sans-serif;font-weight:700;font-size:19px;text-align:center;line-height:22px;padding:0 8px}
.client-1{left:220px;color:var(--red)}
.client-2{left:420px;background:#f5e800;color:#1d1d1d}
.client-3{left:618px;background:var(--red);color:var(--white)}
.client-4{left:818px;background:var(--red-dark);color:#ffd21f}

/* footer */
.site-footer{position:absolute;top:2700px;left:0;width:1200px;height:351px;background:var(--footer)}
.foot-col{position:absolute;top:55px}
.foot-col h4{font-size:13px;font-weight:600;margin-bottom:10px}
.foot-col li{list-style:none;font-size:10.5px;line-height:21px;color:var(--muted)}
.foot-brand{position:absolute;left:848px;top:55px;width:200px}
.foot-brand .brand-name{font-size:30px}
.foot-brand p{margin-top:38px;font-size:10.5px;line-height:19px;color:var(--muted)}
.foot-bottom{position:absolute;left:160px;right:160px;top:244px;border-top:1px solid #d6d6d6;padding-top:28px;font-size:10px;line-height:18px;color:var(--muted)}
.foot-bottom .hl{color:var(--red)}
.social{position:absolute;right:0;top:32px;display:flex;gap:6px}
.social i{width:26px;height:26px;border-radius:50%;display:block}
.live-chat{position:absolute;right:0;top:2825px;width:38px;height:110px;background:var(--red);border-radius:6px 0 0 6px;color:var(--white);font-family:"Raleway",sans-serif;font-weight:700;font-size:11px;writing-mode:vertical-rl;transform:rotate(180deg);display:flex;align-items:center;justify-content:center;letter-spacing:1px}
</style>
</head>
<body>

<header class="site-header">
  <div class="brand"><span class="brand-mark"></span><span class="brand-name">VARNO</span></div>
  <div class="brand-tag">Spark Every Day</div>
  <div class="call">
    <svg width="16" height="14" viewBox="0 0 16 14"><path d="M1 4c0-2 3-3 7-3s7 1 7 3v2h-4V4H5v2H1z M4 7h8l2 6H2z" fill="#ec1f27"/></svg>
    CALL US: 137290 VARNO
  </div>
  <nav class="main-nav">
    <span class="active">Home</span><span>Varno Story</span><span>Our Work</span><span>Contact Us</span><span>Electrical</span><span>LED Lighting</span><span>Solar Power</span>
  </nav>
</header>

<section class="hero" role="img" aria-label="Rows of solar panels in a field under a cloudy sky at sunset">
  <h1 class="hero-title">Varno Electrical<br>Spark Every Day</h1>
  <a class="btn">Get Started Here</a>
  <svg class="hero-arrow" style="left:42px" width="28" height="56" viewBox="0 0 28 56"><path d="M26 2 2 28l24 26" fill="none" stroke="#fff" stroke-width="2" opacity=".7"/></svg>
  <svg class="hero-arrow" style="right:42px" width="28" height="56" viewBox="0 0 28 56"><path d="M2 2l24 26L2 54" fill="none" stroke="#fff" stroke-width="2" opacity=".7"/></svg>
</section>

<section class="block about-copy">
  <h2 class="section-title">About Us</h2><span class="rule"></span>
  <p>Varno Electrical was formed to be an expert Electricity Contracting Company providing services to all Residential and Commercial Customers. With over 10 years of experience, Varno Electrical has developed a highly-experienced team of professionals that ensure all our customer expectations are met. Sed ut perspiciatis unde omnis isteiste natus error vo luptatem accusantium doloremque ilsS ut pertisde omnis isteiste natus Sed ut persluptatem us antium doloremque ilsS ut persciatis un.Sed ut perspiciatis unde omnis isteiste natus error vo luptatem accusantium doloremque ilsS ut pertisde omnis isteiste natus Sed ut persluptatem us antium doloremque ilsS ut persciatis Sd ut perspiciatis unde omnis isteiste natus.</p>
  <a class="btn btn-outline">Read More</a>
</section>
<div class="about-video" role="img" aria-label="Video still of a steel roof structure with warehouse lighting">
  <svg width="475" height="304" viewBox="0 0 475 304"><g transform="translate(237 152)"><circle r="40" fill="#1f1f1f" stroke="#c8141b" stroke-width="6"/><path d="M-11-20 19 0-11 20z" fill="#fff"/></g></svg>
</div>

<section class="services">
  <article class="service" style="left:160px">
    <div class="service-photo" role="img" aria-label="Bundle of coloured electrical cables" style="background:linear-gradient(135deg,#2e5c8a,#b33a2a 50%,#e0a030)"></div>
    <h3>Electrical</h3><span class="rule"></span>
    <p>Sd ut perspiciatis unde omnis iste natus error sit volup tatem accusantium dolormqu e laudan tium, totam re maperiam, eaque ipsa quae ab illo inventore veri tatis et quasi architecto beatae vitae dict</p>
  </article>
  <article class="service" style="left:463px">
    <div class="service-photo" role="img" aria-label="LED light bulbs on grass" style="background:linear-gradient(180deg,#6fa040,#9aa6a8 55%,#3f6a2a)"></div>
    <h3>Led Lighting</h3><span class="rule"></span>
    <p>Sd ut perspiciatis unde omnis iste natus error sit volup tatem accusantium dolormqu e laudan tium, totam re maperiam, eaque ipsa quae ab illo inventore veri tatis et quasi architecto beatae vitae dict</p>
  </article>
  <article class="service" style="left:765px">
    <div class="service-photo" role="img" aria-label="Solar panels under a blue sky" style="background:linear-gradient(180deg,#3d7cc8,#7fb0e0 35%,#25457a 60%,#6a8a3a)"></div>
    <h3>Solar Power</h3><span class="rule"></span>
    <p>Sd ut perspiciatis unde omnis iste natus error sit volup tatem accusantium dolormqu e laudan tium, totam re maperiam, eaque ipsa quae ab illo inventore veri tatis et quasi architecto beatae vitae dict</p>
  </article>
</section>

<section class="block why-title center">
  <h2 class="section-title">Why Choose Us?</h2><span class="rule"></span>
</section>
<div class="reason" style="left:152px"><div class="badge">1</div><h4>Professional Service</h4><p>When you hire a Varno Electrical Electrician you will get a profes sional &amp; well-presented Electr ician that comes skilled.</p></div>
<div class="reason" style="left:333px"><div class="badge">2</div><h4>5 year workmanship guarantee</h4><p>When you hire a Varno Electrical Electrician you will get a profes sional &amp; well-presented Electr ician that comes skilled.</p></div>
<div class="reason" style="left:515px"><div class="badge">3</div><h4>Value for Money</h4><p>We provide extremely compet itive pricing, which means you get value for money on quality that is comparable to the</p></div>
<div class="reason" style="left:696px"><div class="badge">4</div><h4>Environmentally friendly</h4><p>We a committed to reducing carbon emissions by installing Solar Power and upgrading sites to LED Lighting</p></div>
<div class="reason" style="left:877px"><div class="badge">5</div><h4>Fully insured</h4><p>Varno Electrical is fully insured and equipped to handle break downs and service call outs.</p></div>

<section class="reviews">
  <div class="block reviews-title"><h2 class="section-title">Client Reviews</h2><span class="rule"></span></div>
  <blockquote class="quote">
    <span class="quote-mark">&ldquo;</span>
    <p>I found Marcus to be well organised, punctual, professional and a good communicator. He did the job at a very reasonable price. A pleasure to deal with ab illo inventore verit atis et quasi architecto beatae vitae dicta sunt explicabemo enim ipsam voluptatem quia voluptas sit aspernatur autdit aut fugit, sed quia consequuntur magni dolores eos qui ratione volutatm sequi nesciuneque porro voluptas sit aspernatur autdit aut fugit, sed quia consequuntur marouitsquam est.</p>
  </blockquote>
  <div class="reviewer"><span class="stars">★★★★★</span>Lena R. Mount Waverley VIC</div>
  <figure class="review-card">
    <div class="review-card-name"><i></i>HARBURY SIGNWORKS</div>
    <div class="review-card-photo" role="img" aria-label="Interior of a sign workshop with racks and materials"></div>
  </figure>
</section>

<section class="block clients-title center">
  <h2 class="section-title">Our Satisfied Clients Include...</h2><span class="rule"></span>
</section>
<div class="client client-1">Brightlane</div>
<div class="client client-2">Outback Supply Co</div>
<div class="client client-3">Heron Plumbing Supplies</div>
<div class="client client-4">Goldfork Diner</div>

<footer class="site-footer">
  <div class="foot-col" style="left:160px"><h4>Links</h4><ul><li>Sed ut perspiciatis</li><li>Qnde omnis iste n</li><li>Wtus error sit volup</li><li>em accusantiu</li><li>Gdoloremque</li></ul></div>
  <div class="foot-col" style="left:345px"><h4>Let Us Help You</h4><ul><li>Your Account</li><li>Your Orders</li><li>Sed ut perspiciatis nde</li><li>Wtus error sit voluptat</li><li>Saccusantiu</li><li>Gdoloremque</li></ul></div>
  <div class="foot-col" style="left:533px"><h4>Product</h4><ul><li>Led Lighting</li><li>Solar Power</li><li>Electrical</li><li>Career</li><li>Others</li></ul></div>
  <div class="foot-col" style="left:688px"><h4>Company</h4><ul><li>Home</li><li>Varno Story</li><li>Our Work</li><li>Electrical</li><li>Led Lighting</li><li>Solar Power</li></ul></div>
  <div class="foot-brand">
    <div style="display:flex;align-items:center;gap:8px"><span class="brand-mark"></span><span class="brand-name">VARNO</span></div>
    <p>Sed ut perspiciatis unde omnis iste nat us erloror sit volu ptatem accusantium dolo remque laudantium, totam.</p>
  </div>
  <div class="foot-bottom">
    <div>© 2017 All Copyrights are Reserved | <span class="hl">Varno Electrical.</span></div>
    <div>Terms of Use &nbsp; Privacy Policy &nbsp; Sitemap &nbsp; Contact Us</div>
    <div class="social"><i style="background:#3aa0d8"></i><i style="background:#3b5998"></i><i style="background:#1f6fa8"></i><i style="background:#d8453a"></i></div>
  </div>
</footer>

<div class="live-chat">LIVE CHAT</div>

</body>
</html>
```